Redesign of business card for Cedar Ridge Mechanical

We are looking for a new design for our business cards for Cedar Ridge Mechanical. We are a plumbing & HVAC construction company, operating on the West Coast of Canada and USA. Logo attached.
Industry/Entity Type
Construction - Plumbing & HVAC
Contact Information for Business Card
Name, address, phone numbers, email, website address
Look and feel
Each slider illustrates characteristics of the customer's brand and the style your logo design should communicate.

```html
<!DOCTYPE html>
<html lang="en">
<head>
<meta charset="utf-8">
<title>Cedar Ridge Mechanical – Business Card</title>
<link rel="stylesheet" href="https://fonts.googleapis.com/css2?family=Poppins:wght@400;600;700&display=swap">
<style>
  :root {
    --stage: #232323;
    --card-light: #e4e5e4;
    --card-dark: #0f0f10;
    --card-dark-mid: #1c1c1d;
    --card-dark-sheen: #4a4a4c;
    --card-edge: #3a3a3b;
    --ink: #111111;
  }
  * { margin: 0; padding: 0; box-sizing: border-box; }
  html, body {
    width: 1200px; height: 780px; overflow: hidden;
    background: var(--stage);
    font-family: "Poppins", sans-serif;
  }
  .stage {
    position: relative; width: 1200px; height: 780px;
    display: flex; align-items: center; justify-content: center; gap: 40px;
  }
  .card {
    position: relative; width: 540px; height: 309px;
    border-radius: 4px; overflow: hidden;
  }
  .card-front { background: var(--card-light); color: var(--ink); }
  .person { position: absolute; left: 30px; top: 28px; }
  .person-name { font-size: 26px; line-height: 1.1; font-weight: 400; }
  .person-name .first { font-weight: 700; }
  .person-role { font-size: 12px; margin-top: 4px; }
  .brand {
    position: absolute; right: 32px; top: 104px;
    display: flex; align-items: center; gap: 10px;
  }
  .brand-square { width: 22px; height: 22px; background: var(--ink); }
  .brand-name { font-size: 19px; font-weight: 600; letter-spacing: 0.3px; }
  .contact {
    position: absolute; right: 32px; bottom: 26px;
    text-align: right; font-size: 13.5px; line-height: 1.45;
  }
  .contact-address { margin-bottom: 8px; }
  .contact-line { display: flex; align-items: center; justify-content: flex-end; gap: 10px; }
  .contact-line svg { width: 15px; height: 15px; flex: none; }
  .card-back {
    background:
      radial-gradient(ellipse 70% 80% at 85% 15%, var(--card-dark-sheen) 0%, transparent 70%),
      linear-gradient(135deg, var(--card-dark-mid) 0%, var(--card-dark) 100%);
    box-shadow: inset 0 0 0 1px var(--card-edge);
  }
</style>
</head>
<body>
<main class="stage">
  <section class="card card-front" aria-label="Business card front">
    <div class="person">
      <p class="person-name"><span class="first">Marta</span> Velenska</p>
      <p class="person-role">Founder &amp; CEO</p>
    </div>
    <div class="brand">
      <span class="brand-square" aria-hidden="true"></span>
      <span class="brand-name">Cedar Ridge Mechanical</span>
    </div>
    <div class="contact">
      <p class="contact-address">418 Harbor Line Rd. Suite 120<br>Tacoma, WA 98402</p>
      <p class="contact-line">(253) 555-0147
        <svg viewBox="0 0 16 16" aria-hidden="true"><circle cx="8" cy="8" r="8" fill="#111"/><path d="M5 4.2l1.6-.4.9 2.1-1 .8c.5 1.1 1.3 1.9 2.4 2.4l.8-1 2.1.9-.4 1.6c-3.4.1-6.5-3-6.4-6.4z" fill="#e4e5e4"/></svg>
      </p>
      <p class="contact-line">info@cedarridgemech.com
        <svg viewBox="0 0 16 16" aria-hidden="true"><circle cx="8" cy="8" r="8" fill="#111"/><rect x="3.8" y="5" width="8.4" height="6" fill="none" stroke="#e4e5e4" stroke-width="1.1"/><path d="M3.8 5l4.2 3.4L12.2 5" fill="none" stroke="#e4e5e4" stroke-width="1.1"/></svg>
      </p>
      <p class="contact-line">www.cedarridgemech.com
        <svg viewBox="0 0 16 16" aria-hidden="true"><circle cx="8" cy="8" r="8" fill="#111"/><circle cx="8" cy="8" r="4.4" fill="none" stroke="#e4e5e4" stroke-width="1"/><ellipse cx="8" cy="8" rx="2" ry="4.4" fill="none" stroke="#e4e5e4" stroke-width="1"/><path d="M3.6 8h8.8" stroke="#e4e5e4" stroke-width="1"/></svg>
      </p>
    </div>
  </section>
  <section class="card card-back" role="img" aria-label="Business card back: repeating brand mark pattern in glossy grey on black"></section>
</main>
</body>
</html>
```